Web Developer Needs a Business Card Design

I need a personal business card design that represents me as a web developer for potential employers. I would like the background to be a dark color on the front for contrast with my logo and name. The back will have all my information along with a smaller version of the logo. I want something with a modern look and feel, not too conservative. This will be used for potential employers and freelance work.

Industry/Entity Type

Business

Contact Information for Business Card

Front should have my logo and name. The back should have all my personal information which would include: name: Tom Varulek, phone: 570-614-3098, email: tomvarulek@quillbox.net, website url: www.tomvarulek.net, logo, web developer.

Font styles to use
Sans Serif

Requirements
Must have
• Must include my logo. The color palette base color will be the logo color.

```html
<!DOCTYPE html>
<html lang="en">
<head>
<meta charset="UTF-8">
<title>Tom Varulek — Business Card</title>
<link rel="stylesheet" href="https://fonts.googleapis.com/css2?family=Lato:wght@400;700&display=swap">
<style>
  :root {
    --brand-green: #248c72;
    --card-dark: #1b1311;
    --page-bg: #1c1c1c;
    --card-light: #ffffff;
    --ink: #1e1e1e;
  }
  html, body {
    margin: 0;
    padding: 0;
    width: 1200px;
    height: 1086px;
    overflow: hidden;
    background: var(--page-bg);
    font-family: "Lato", sans-serif;
  }
  .canvas {
    position: relative;
    width: 1200px;
    height: 1086px;
  }
  .card {
    position: absolute;
    left: 254px;
    width: 677px;
    border-radius: 8px;
    overflow: hidden;
  }
  .card--front {
    top: 126px;
    height: 387px;
    background: var(--card-light);
  }
  .card--back {
    top: 588px;
    height: 384px;
    background: var(--card-dark);
  }
  .brand-ring {
    position: absolute;
    border-radius: 50%;
    box-sizing: border-box;
    border-style: solid;
    border-color: var(--brand-green);
  }
  .card--front .brand-ring {
    left: 138px;
    top: 118px;
    width: 116px;
    height: 116px;
    border-width: 8px;
  }
  .brand-name {
    position: absolute;
    margin: 0;
    color: var(--brand-green);
    font-weight: 700;
    text-align: center;
    white-space: nowrap;
  }
  .card--front .brand-name {
    left: 96px;
    width: 200px;
    top: 248px;
    font-size: 29px;
    line-height: 1;
  }
  .divider {
    position: absolute;
    left: 338px;
    top: 128px;
    width: 2px;
    height: 132px;
    background: linear-gradient(to bottom, var(--brand-green) 0 33%, var(--ink) 33% 100%);
  }
  .contact {
    position: absolute;
    left: 366px;
    top: 128px;
    color: var(--ink);
  }
  .contact__name {
    margin: 0;
    font-size: 27px;
    font-weight: 700;
    color: var(--brand-green);
    line-height: 1.1;
  }
  .contact__title {
    margin: 1px 0 0;
    font-size: 21px;
    line-height: 1.2;
  }
  .contact__list {
    list-style: none;
    margin: 26px 0 0;
    padding: 0;
    font-size: 22px;
    line-height: 27px;
  }
  .contact__list li {
    display: flex;
    align-items: center;
    gap: 8px;
  }
  .contact__list svg {
    width: 20px;
    height: 16px;
    fill: var(--brand-green);
    flex: none;
  }
  .footer-band {
    position: absolute;
    left: 0;
    bottom: 0;
    width: 100%;
    height: 23px;
    display: flex;
  }
  .footer-band__accent {
    width: 453px;
    background: var(--brand-green);
  }
  .footer-band__url {
    flex: 1;
    background: var(--card-dark);
    color: #fff;
    font-size: 16px;
    line-height: 23px;
    padding-left: 22px;
  }
  .card--back .brand-ring {
    left: 280px;
    top: 116px;
    width: 118px;
    height: 118px;
    border-width: 11px;
  }
  .card--back .brand-name {
    left: 189px;
    width: 300px;
    top: 258px;
    font-size: 30px;
    line-height: 1;
  }
  .back-url {
    position: absolute;
    left: 0;
    width: 100%;
    top: 338px;
    margin: 0;
    text-align: center;
    color: #fff;
    font-size: 22px;
    letter-spacing: 0.5px;
  }
  .back-url__name {
    color: var(--brand-green);
  }
</style>
</head>
<body>
<main class="canvas">
  <section class="card card--front" aria-label="Card front">
    <div class="brand-ring" aria-hidden="true"></div>
    <p class="brand-name">TOM VARULEK</p>
    <div class="divider" aria-hidden="true"></div>
    <div class="contact">
      <h1 class="contact__name">Tom Varulek</h1>
      <p class="contact__title">President</p>
      <ul class="contact__list">
        <li>
          <svg viewBox="0 0 20 16" aria-hidden="true"><path d="M1 5c0-3 4-4 9-4s9 1 9 4v2h-4V5c-1-1-9-1-10 0v2H1z"/><path d="M5 7h10l3 8H2z"/></svg>
          <span>570-614-3098</span>
        </li>
        <li>
          <svg viewBox="0 0 20 16" aria-hidden="true"><path d="M1 2h18v12H1z M3 4v.5l7 5 7-5V4zm0 3v5h14V7l-7 5z" fill-rule="evenodd"/></svg>
          <span>tomvarulek@quillbox.net</span>
        </li>
      </ul>
    </div>
    <div class="footer-band">
      <div class="footer-band__accent"></div>
      <div class="footer-band__url">www.tomvarulek.net</div>
    </div>
  </section>

  <section class="card card--back" aria-label="Card back">
    <div class="brand-ring" aria-hidden="true"></div>
    <p class="brand-name">TOM VARULEK</p>
    <p class="back-url">www.<span class="back-url__name">tomvarulek</span>.net</p>
  </section>
</main>
</body>
</html>
```